Salon and Spa Distributor Business Card

Need a business card. We are are distributor in the salon and spa industry. We identify with natural beauty. Need a card with:
Company Name: Petal Quarry"
Title: "President & CEO"
Address
Company Phone number
email
website
Tag Line:" The Professional Salon Source"

Industry/Entity Type

Business

Contact Information for Business Card

Name: Dov Strommen
Title: "President & CEO"
Address: 31 Harlow Ln, Bexmoor, NJ 07813
Company Phone number: 800-463-5918
email: dovstrommen@petalquarry.example
website: www.petalquarry.example

Requirements
Should not have
• No black backgrounds

```html
<!DOCTYPE html>
<html lang="en">
<head>
<meta charset="utf-8">
<title>Petal Quarry — Business Card</title>
<link rel="stylesheet" href="https://fonts.googleapis.com/css2?family=Questrial&display=swap">
<style>
  :root {
    --backdrop: #e6e6e6;
    --green-deep: #005a26;
    --green-mid: #1a7a3a;
    --green-soft: #2f8a45;
    --green-bright: #3fae3a;
    --green-band: #3cb43c;
    --paper: #f7f7f5;
    --ink-light: #ffffff;
  }
  * { margin: 0; padding: 0; box-sizing: border-box; }
  html, body {
    width: 1200px; height: 576px; overflow: hidden;
    background: var(--backdrop);
    font-family: "Questrial", "Century Gothic", sans-serif;
  }
  .canvas { position: relative; width: 1200px; height: 576px; }

  .card {
    position: absolute; top: 139px;
    width: 484px; height: 291px;
    border-radius: 14px; overflow: hidden;
  }

  /* Front */
  .card-front {
    left: 82px;
    background: linear-gradient(180deg, var(--green-deep) 0%, var(--green-mid) 55%, var(--green-soft) 100%);
    color: var(--ink-light);
    display: flex; flex-direction: column; align-items: center; justify-content: center;
  }
  .front-mark {
    width: 58px; height: 58px; border-radius: 50%;
    background: var(--ink-light);
    margin-bottom: 18px; margin-top: 6px;
  }
  .front-name { font-size: 30px; letter-spacing: 0.2px; }

  /* Back */
  .card-back { left: 602px; background: var(--paper); }
  .back-shape { position: absolute; inset: 0; }
  .back-info { position: absolute; left: 20px; top: 0; color: var(--ink-light); }
  .company-name { position: absolute; top: 27px; font-size: 26px; white-space: nowrap; }
  .job-title { position: absolute; top: 58px; font-size: 11px; white-space: nowrap; }
  .contact-list { position: absolute; top: 163px; list-style: none; font-size: 13px; white-space: nowrap; }
  .contact-list li { display: flex; align-items: center; height: 18px; margin-bottom: 1px; }
  .contact-list .icon { width: 12px; height: 12px; margin-right: 10px; flex: none; }
  .contact-list .address { margin-top: 3px; }
  .tagline {
    position: absolute; left: 20px; top: 248px;
    font-size: 13px; color: var(--ink-light); white-space: nowrap;
  }
  .back-name {
    position: absolute; left: 300px; width: 181px; top: 132px;
    text-align: center; font-size: 20px; color: var(--green-bright);
  }
</style>
</head>
<body>
<div class="canvas">

  <section class="card card-front" aria-label="Card front">
    <div class="front-mark" aria-hidden="true"></div>
    <div class="front-name">Petal Quarry</div>
  </section>

  <section class="card card-back" aria-label="Card back">
    <svg class="back-shape" width="484" height="291" viewBox="0 0 484 291" aria-hidden="true">
      <defs>
        <linearGradient id="panelFill" x1="0" y1="0" x2="0" y2="1">
          <stop offset="0" stop-color="#005a26"/>
          <stop offset="1" stop-color="#2f8a45"/>
        </linearGradient>
      </defs>
      <path d="M0 0 H322 Q238 145 318 291 H0 Z" fill="url(#panelFill)"/>
      <rect x="0" y="245" width="300" height="25" fill="#3cb43c"/>
      <path d="M340 0 H352 Q272 140 318 291 H314 Q258 150 340 0 Z" fill="#3fae3a"/>
    </svg>

    <div class="back-info">
      <div class="company-name">Petal Quarry</div>
      <div class="job-title">President &amp; CEO</div>
      <ul class="contact-list">
        <li>
          <svg class="icon" viewBox="0 0 12 12" aria-hidden="true"><path d="M1 4 Q6 0 11 4 L9.5 5.5 L8 4.5 L8 3.5 Q6 3 4 3.5 L4 4.5 L2.5 5.5 Z M3 6 H9 L10 11 H2 Z" fill="#fff"/></svg>
          800-463-5918
        </li>
        <li>
          <svg class="icon" viewBox="0 0 12 12" aria-hidden="true"><rect x="0.5" y="2.5" width="11" height="7.5" fill="#fff"/><path d="M0.5 2.5 L6 7 L11.5 2.5" fill="none" stroke="#1a7a3a" stroke-width="1"/></svg>
          dovstrommen@petalquarry.example
        </li>
        <li>
          <svg class="icon" viewBox="0 0 12 12" aria-hidden="true"><g fill="none" stroke="#fff" stroke-width="1"><circle cx="6" cy="6" r="5"/><ellipse cx="6" cy="6" rx="2.2" ry="5"/><path d="M1 6 H11 M2 3.5 H10 M2 8.5 H10"/></g></svg>
          www.petalquarry.example
        </li>
        <li class="address">31 Harlow Ln, Bexmoor, NJ 07813</li>
      </ul>
    </div>
    <div class="tagline">The Professional Salon Source</div>
    <div class="back-name">Petal Quarry</div>
  </section>

</div>
</body>
</html>
```